Boutique custom software development company needs new business card

Our nearly 20 year old custom software development company would like to better include the fact that we are now providing Bitcoin services. These new services are B2B include education (how to acquire and securely hold Bitcoin) and integrating Bitcoin payments into existing ecommerce sites or other existing systems. Please keep the card clean and simple. Attached is our current design and some other files. vextorial.com

Target Market(s)

businesses owners interested in long term relationship

Industry/Entity Type

Custom software development and Bitcoin

Contact Information for Business Card

Dale Parker, dale@vextorial.com, vextorial.com, (888) 555-VXTRL

Font styles to use
Other font styles liked:
• monospace

Requirements
Must have
• double-sided
Nice to have
• clean and simple
Should not have
• physical address

```html
<!DOCTYPE html>
<html lang="en">
<head>
<meta charset="utf-8">
<title>Vextorial business card</title>
<link rel="stylesheet" href="https://fonts.googleapis.com/css2?family=Montserrat:wght@400;500;700&family=Open+Sans:wght@400&display=swap">
<style>
  :root {
    --backdrop: #7d7d7b;
    --paper: #ffffff;
    --brand-blue: #3e72b8;
    --brand-blue-deep: #2f5fa3;
    --accent-orange: #ee7623;
    --ink-grey: #555a60;
  }
  * { box-sizing: border-box; margin: 0; padding: 0; }
  html, body {
    width: 1200px; height: 801px; overflow: hidden;
    background: var(--backdrop);
  }
  .sheet {
    width: 1200px; height: 801px;
    display: flex; align-items: center; justify-content: center; gap: 36px;
  }
  .card {
    position: relative;
    width: 560px; height: 320px;
    box-shadow: 0 10px 24px rgba(0,0,0,.25);
  }
  .card--front { background: var(--paper); border-bottom: 3px solid var(--brand-blue); }
  .card--back { background: var(--brand-blue); }

  .brand { position: absolute; left: 48px; top: 70px; }
  .brand__name {
    font-family: "Montserrat", sans-serif; font-weight: 700;
    font-size: 50px; line-height: 1; letter-spacing: 1px;
    color: var(--brand-blue);
  }
  .brand__tagline {
    margin-top: 4px;
    font-family: "Open Sans", sans-serif; font-size: 15px;
    color: var(--brand-blue);
  }

  .holder {
    position: absolute; right: 34px; top: 168px;
    font-family: "Montserrat", sans-serif; font-weight: 700;
    font-size: 18px; letter-spacing: .5px; text-transform: uppercase;
    color: var(--brand-blue);
  }
  .divider {
    position: absolute; left: 28px; right: 20px; top: 200px;
    height: 1px; background: var(--brand-blue);
  }

  .contacts { position: absolute; left: 34px; top: 214px; list-style: none; }
  .contacts li {
    display: flex; align-items: center; gap: 9px;
    font-family: "Montserrat", sans-serif; font-size: 15px; line-height: 22px;
    color: var(--ink-grey);
  }
  .contacts svg { width: 11px; height: 11px; fill: var(--accent-orange); flex: none; }

  .back-mark {
    position: absolute; left: 50%; top: 50%; transform: translate(-50%, -50%);
    display: flex; align-items: center; gap: 14px;
  }
  .back-mark__square { width: 44px; height: 44px; background: var(--brand-blue-deep); }
  .back-mark__name {
    font-family: "Montserrat", sans-serif; font-weight: 700; font-size: 40px;
    color: var(--brand-blue-deep);
  }
</style>
</head>
<body>
<main class="sheet">
  <section class="card card--front" aria-label="Card front">
    <div class="brand">
      <div class="brand__name">Vextorial</div>
      <div class="brand__tagline">developer of custom applications</div>
    </div>
    <div class="holder">Dale Parker</div>
    <div class="divider"></div>
    <ul class="contacts">
      <li>
        <svg viewBox="0 0 12 12" aria-hidden="true"><path d="M2.5 1l2 2.2-1.2 1.3a7 7 0 0 0 4.2 4.2l1.3-1.2 2.2 2-1.4 1.5C5 10.5 1.5 7 .9 2.4z"/></svg>
        (888) 555-VXTRL
      </li>
      <li>
        <svg viewBox="0 0 12 12" aria-hidden="true"><path d="M0 2h12v8H0z M0 2l6 4.5L12 2" stroke="#fff" stroke-width=".8"/></svg>
        dale@vextorial.com
      </li>
      <li>
        <svg viewBox="0 0 12 12" aria-hidden="true"><circle cx="6" cy="6" r="6"/><path d="M0 6h12M6 0c-3 3-3 9 0 12M6 0c3 3 3 9 0 12" stroke="#fff" stroke-width=".8" fill="none"/></svg>
        www.vextorial.com
      </li>
    </ul>
  </section>

  <section class="card card--back" aria-label="Card back">
    <div class="back-mark">
      <div class="back-mark__square"></div>
      <div class="back-mark__name">Vextorial</div>
    </div>
  </section>
</main>
</body>
</html>
```